Corvane Holdings , new business card design

investment firm with corporate clients . need double sided business card , vertical and horizontal options ,logo must be clear. prefer pantone colors only and sharp design. website also www.corvane.ae

Khalid Bin Tarrafi
Managing Director
Tel. +971 4 387 2940
Mobile +971 50 518 2403
khalid@corvane.ae
Q-Span Plaza, officw 18-B07, Warqa Gardens, Dubai

Contact Information for Business Card

Khalid Bin Tarrafi
Managing Director

Font styles to use
Serif

Colors

Designer to choose colors to be used in the design.

```html
<!DOCTYPE html>
<html lang="en">
<head>
<meta charset="utf-8">
<title>Corvane Holdings – Business Card</title>
<link rel="stylesheet" href="https://fonts.googleapis.com/css2?family=Montserrat:wght@700&family=Questrial&display=swap">
<style>
  :root {
    --brand-blue: #4a7199;
    --paper: #fbfbfb;
    --ink: #4f5052;
    --backdrop: #e6e2de;
  }
  * { box-sizing: border-box; margin: 0; padding: 0; }
  html, body {
    width: 1200px; height: 997px; overflow: hidden;
    background: var(--backdrop);
    font-family: "Questrial", "Century Gothic", sans-serif;
  }
  .sheet {
    width: 1200px; height: 997px;
    display: flex; flex-direction: column;
    align-items: center; justify-content: center; gap: 56px;
  }
  .card {
    position: relative;
    width: 660px; height: 377px;
    box-shadow: 0 2px 6px rgba(0,0,0,.12);
  }
  .card--front { background: var(--paper); }
  .card--back { background: var(--brand-blue); display: flex; align-items: center; justify-content: center; }

  .wordmark {
    display: flex; align-items: center; gap: 12px;
    font-family: "Questrial", sans-serif;
    letter-spacing: .28em; text-transform: uppercase;
  }
  .wordmark__mark { width: 12px; height: 12px; background: currentColor; }
  .card--front .wordmark {
    position: absolute; top: 46px; right: 34px;
    color: var(--brand-blue); font-size: 22px;
  }
  .card--back .wordmark { color: #fff; font-size: 34px; }

  .name-plate {
    position: absolute; top: 112px; left: 18px;
    width: 262px; height: 58px;
    background: var(--brand-blue); color: #fff;
    padding: 10px 0 0 30px;
  }
  .name-plate__name {
    font-family: "Montserrat", sans-serif; font-weight: 700;
    font-size: 13px; letter-spacing: .02em; text-transform: uppercase;
  }
  .name-plate__title { font-size: 14px; margin-top: 3px; }

  .address {
    position: absolute; top: 142px; right: 34px;
    text-align: right; color: var(--ink);
    font-size: 14px; line-height: 1.35; font-style: normal;
  }

  .contacts {
    position: absolute; top: 268px; left: 148px;
    list-style: none; color: var(--ink); font-size: 15px; line-height: 1.25;
  }
  .contacts li { display: flex; align-items: center; gap: 8px; }
  .contacts svg { width: 11px; height: 11px; fill: var(--brand-blue); flex: none; }
</style>
</head>
<body>
<main class="sheet">
  <section class="card card--front">
    <div class="wordmark"><span class="wordmark__mark"></span>Corvane Holdings</div>

    <div class="name-plate">
      <p class="name-plate__name">Khalid Bin Tarrafi</p>
      <p class="name-plate__title">Managing Director</p>
    </div>

    <address class="address">
      Q-Span Plaza, officw 18-B07,<br>
      Warqa Gardens, Dubai
    </address>

    <ul class="contacts">
      <li>
        <svg viewBox="0 0 12 12" aria-hidden="true"><path d="M2.5 1 4.5 3.2 3.4 4.6c.7 1.6 2 2.9 3.6 3.6l1.4-1.1L10.6 9 9.2 11C5 10.6 1.4 7 1 2.8z"/></svg>
        +971 4 387 2940
      </li>
      <li>
        <svg viewBox="0 0 12 12" aria-hidden="true"><path d="M3 0h6a1 1 0 0 1 1 1v10a1 1 0 0 1-1 1H3a1 1 0 0 1-1-1V1a1 1 0 0 1 1-1zm.5 1.5v8h5v-8z"/></svg>
        +971 50 518 2403
      </li>
      <li>
        <svg viewBox="0 0 12 12" aria-hidden="true"><path d="M0 2h12v8H0zm1.2 1.1v.3L6 6.6l4.8-3.2v-.3z"/></svg>
        khalid@corvane.ae
      </li>
    </ul>
  </section>

  <section class="card card--back">
    <div class="wordmark"><span class="wordmark__mark"></span>Corvane Holdings</div>
  </section>
</main>
</body>
</html>
```